Business Card Design Project

The business card is for an educational company that provides personalised tuition to students.

The company logo is in orange and blue (as provided) and should be included in the name card design

The philosophy of the company is to make learning a comfortable experience for student as such design of the namecard should look fresh and has a bit of the 'wow' factor. Some of the namecard design that appeals to me are as uploaded under Sample Design.

The particulars that need to be provided are:
(1): Company Name (Lantern Education)
(1): Name
(2): Educational qualifications which will appear below name
(3): Mobile number
(4): Email address
(5): Website

Industry/Entity Type

Business

Requirements
Must have
• (1): Company Logo

(2): The card background should preferably be coloured both for the front side and back.

(3): The choice of font is important as part of the selection consideration. There is no preferred font that I have selected, designer is free to choose the font that will complement their design.

```html
<!DOCTYPE html>
<html lang="en">
<head>
<meta charset="utf-8">
<title>Lantern Education – Business Card</title>
<link rel="stylesheet" href="https://fonts.googleapis.com/css2?family=Sorts+Mill+Goudy&family=Libre+Baskerville:wght@700&display=swap">
<style>
  :root {
    --page-bg: #2a2a2a;
    --card-blue-light: #3aa0dc;
    --card-blue: #2487c6;
    --card-blue-deep: #1a6fae;
    --accent-orange: #f07a1a;
    --accent-orange-deep: #d9560f;
    --paper-white: #ffffff;
    --ink-grey: #4a4a4a;
  }
  * { margin: 0; padding: 0; box-sizing: border-box; }
  html, body { width: 1200px; height: 900px; overflow: hidden; }
  body {
    background: var(--page-bg);
    font-family: "Sorts Mill Goudy", Georgia, serif;
  }
  .canvas {
    position: relative;
    width: 1200px;
    height: 900px;
  }
  .card {
    position: absolute;
    left: 250px;
    width: 700px;
    height: 400px;
    overflow: hidden;
    box-shadow: 0 10px 28px rgba(0,0,0,0.45);
  }
  .card--back {
    top: 40px;
    background: radial-gradient(circle at 50% 40%, var(--card-blue-light) 0%, var(--card-blue) 45%, var(--card-blue-deep) 100%);
  }
  .card--front {
    top: 470px;
    background: var(--paper-white);
  }
  .brand {
    position: absolute;
    display: flex;
    align-items: center;
  }
  .brand__mark {
    background: var(--accent-orange);
    flex: none;
  }
  .brand__name {
    font-family: "Libre Baskerville", Georgia, serif;
    font-weight: 700;
    line-height: 1.02;
  }
  .card--back .brand {
    left: 150px;
    top: 110px;
    gap: 22px;
  }
  .card--back .brand__mark { width: 96px; height: 96px; }
  .card--back .brand__name {
    color: var(--paper-white);
    font-size: 44px;
  }
  .back__website {
    position: absolute;
    left: 0;
    right: 0;
    bottom: 44px;
    text-align: center;
    color: var(--paper-white);
    font-size: 22px;
    letter-spacing: 0.5px;
  }
  .front__wave {
    position: absolute;
    inset: 0;
    width: 700px;
    height: 400px;
  }
  .card--front .brand {
    left: 70px;
    top: 40px;
    gap: 16px;
  }
  .card--front .brand__mark { width: 70px; height: 70px; }
  .card--front .brand__name {
    color: var(--ink-grey);
    font-size: 30px;
  }
  .contact {
    position: absolute;
    right: 60px;
    top: 180px;
    text-align: right;
    color: var(--paper-white);
  }
  .contact__name { font-size: 38px; line-height: 1.1; }
  .contact__role { font-size: 20px; margin-bottom: 22px; }
  .contact__line { font-size: 21px; line-height: 1.3; letter-spacing: 0.4px; }
</style>
</head>
<body>
<main class="canvas">

  <section class="card card--back" aria-label="Business card, back">
    <div class="brand">
      <span class="brand__mark"></span>
      <p class="brand__name">Lantern<br>Education</p>
    </div>
    <p class="back__website">www.lanterneducation.com</p>
  </section>

  <section class="card card--front" aria-label="Business card, front">
    <svg class="front__wave" viewBox="0 0 700 400" aria-hidden="true">
      <defs>
        <radialGradient id="frontBlue" cx="0.35" cy="0.65" r="0.8">
          <stop offset="0" stop-color="#3aa0dc"/>
          <stop offset="0.5" stop-color="#2487c6"/>
          <stop offset="1" stop-color="#1a6fae"/>
        </radialGradient>
        <linearGradient id="waveOrange" x1="0" y1="0" x2="1" y2="0">
          <stop offset="0" stop-color="#d9560f"/>
          <stop offset="0.5" stop-color="#f07a1a"/>
          <stop offset="1" stop-color="#d9560f"/>
        </linearGradient>
      </defs>
      <path d="M0 155 C 150 205, 300 200, 430 165 S 620 112, 700 118 L700 400 L0 400 Z" fill="url(#frontBlue)"/>
      <path d="M0 155 C 150 205, 300 200, 430 165 S 620 112, 700 118" fill="none" stroke="url(#waveOrange)" stroke-width="6"/>
    </svg>

    <div class="brand">
      <span class="brand__mark"></span>
      <p class="brand__name">Lantern<br>Education</p>
    </div>

    <div class="contact">
      <p class="contact__name">Marcus Hale</p>
      <p class="contact__role">General manager</p>
      <p class="contact__line">555 210 4477</p>
      <p class="contact__line">55510880</p>
      <p class="contact__line">info@lanterneducation.com</p>
      <p class="contact__line">www.lanterneducation.com</p>
    </div>
  </section>

</main>
</body>
</html>
```